Website for Swedish wellness company "Heartmeadow"

We need a website for our Swedish wellness company. The name is "Heartmeadow" . The company is all about sustainablility for our body, soul and planet. We work with coaching, yoga, massage, healthy food, retreats(sports, excercise, sufing), healing and inspirational talks. We are convinced that personal sustainability and a strong spiritual connection to yourself will lead to planetary sustainability. Our customers are both companies and consumers from all over the world. The final design should be clean/simple and you should get a feeling of community, happiness, warmth, connection,, joy, spirituality but still a professional touch.Just got a logo from Pixel Harbor and are very happy with it;-)
Updates

Sorry I was too enthusiastic posting this project. Of course I will give you some text as well för the different pages! I will see to that it is finished by friday so if you want to wait with your submissions please do! Best regards Maria

Target Market(s)

Businesses and consumers

Industry/Entity Type

Health And Wellness

Number of Pages Required

5+ page

Font styles to use
Sans Serif

Colors
33a6d7
00a990
b7a5cd

Requirements
Must have
• Idea about pages:
• I am not sure how many pages I get for the price, but 5 would be nice to start with.
• Not sure what write ups is;-)
• But title of the pages could be:
• Landing page
• About us
• Services
• Retreats
• Contact us
Nice to have
• A clean and professional website but with some heart and soul in it. Because we Would love colours that harmonize with our logo, but other ideas are welcome!

```html
<!DOCTYPE html>
<html lang="en">
<head>
<meta charset="utf-8">
<title>Heartmeadow – Wellness for body, soul and planet</title>
<link rel="stylesheet" href="https://fonts.googleapis.com/css2?family=Montserrat:wght@500;600;700;800;900&family=Lato:wght@400;700&display=swap">
<style>
:root{
  --navy:#10295a;
  --navy-deep:#0c2250;
  --teal:#00a990;
  --teal-dark:#16917c;
  --mint:#8dd8c6;
  --lavender:#b7a5cd;
  --lavender-soft:#d9cfe6;
  --blue:#33a6d7;
  --ink:#2a2f3a;
  --muted:#555c66;
  --paper:#ffffff;
  --mist:#f3f3f4;
  --head:'Montserrat',Arial,sans-serif;
  --body:'Lato',Arial,sans-serif;
}
*{box-sizing:border-box;margin:0;padding:0}
html,body{width:1200px;height:3547px;overflow:hidden;background:var(--paper)}
body{font-family:var(--body);color:var(--ink)}
.page{position:relative;width:1200px;height:3547px;overflow:hidden}
.abs{position:absolute}

/* header + hero */
.hero-photo{left:0;top:0;width:1200px;height:716px;
  background:linear-gradient(180deg,#e4f1ef 0%,#d3e8e6 30%,#c9dfe0 42%,#a9c8cf 55%,#8fb3bf 75%,#7ea7b3 100%)}
.hero-figure{left:680px;top:110px;width:300px;height:500px;border-radius:150px 150px 40px 40px;
  background:linear-gradient(180deg,rgba(255,255,255,.0),rgba(240,244,244,.55) 40%,rgba(235,240,240,.75))}
.brand{left:172px;top:18px;display:flex;flex-direction:column;align-items:center;gap:6px}
.brand-dot{width:54px;height:54px;border-radius:50%;background:var(--teal)}
.brand-name{font-family:var(--head);font-weight:600;font-size:19px;letter-spacing:.5px;color:var(--navy)}
.contact-bar{top:26px;display:flex;align-items:center;gap:8px;font-family:var(--head);font-size:14px;font-weight:500;color:var(--navy)}
.contact-ico{width:34px;height:34px;border-radius:50%;border:2px solid var(--teal);display:flex;align-items:center;justify-content:center}
.nav{top:76px;left:0;width:1200px;font-family:var(--head);font-weight:600;font-size:15px;color:var(--navy)}
.nav span{position:absolute}
.hero-title{left:172px;top:252px;font-family:var(--head);font-weight:800;font-size:57px;line-height:68px;color:var(--navy)}
.btn{left:179px;top:415px;width:122px;height:34px;border-radius:17px;background:var(--teal-dark);color:#fff;
  font-family:var(--head);font-weight:700;font-size:12.5px;display:flex;align-items:center;justify-content:center}
.slider{left:526px;top:591px;display:flex;gap:3px}
.slider i{display:block;width:35px;height:4px;background:#4a5058}
.slider i.on{background:#1d2128}

/* section headings */
.sec-title{left:0;width:1200px;text-align:center;font-family:var(--head);font-weight:600;font-size:28px;color:var(--navy)}
.sec-rule{left:563px;width:74px;height:3px;background:var(--teal)}

/* about */
.pillar{width:250px;text-align:center}
.pillar h3{font-family:var(--head);font-weight:600;font-size:20px;margin-top:0}
.pillar p{font-size:11.5px;line-height:20px;color:var(--muted);margin-top:18px}
.pillar .more{font-family:var(--head);font-weight:700;font-size:11px;margin-top:10px}
.pillar svg{display:block;margin:0 auto 24px}
.divider-v{width:1px;height:247px;background:#dcdcdc;top:888px}

/* services */
.services-photo{left:0;top:1211px;width:1200px;height:780px;
  background:linear-gradient(180deg,#9b8fbf 0%,#8a8fbd 30%,#5e9cb0 55%,#24a48c 80%,#1a9d82 100%)}
.svc{width:210px;text-align:center;color:#fff}
.svc svg{display:block;margin:0 auto 6px}
.svc h4{font-family:var(--head);font-weight:600;font-size:20px;line-height:23px}
.svc p{font-size:11px;line-height:20px;margin-top:14px;color:rgba(255,255,255,.92)}

/* blog */
.blog-img{border-radius:0}
.post h5{font-family:var(--head);font-weight:600;font-size:16px;line-height:23px;color:var(--navy);letter-spacing:.2px}
.post p{font-size:11px;line-height:19px;color:var(--muted)}
.post .date{font-family:var(--head);font-weight:700;font-size:12.5px;color:var(--teal-dark)}

/* testimonial */
.quote-band{left:0;top:2656px;width:1200px;height:430px;background:var(--mist)}
.ghost-quote{font-family:Georgia,serif;font-size:330px;line-height:1;color:#e7e8ea;font-weight:700}
.quote-mark{font-family:Georgia,serif;font-weight:700;font-size:74px;line-height:1;color:var(--teal-dark)}
.quote-text{left:300px;top:2820px;width:640px;font-family:var(--head);font-style:italic;font-weight:500;font-size:14.5px;line-height:25.7px;color:#3b3f47}
.quote-name{left:300px;top:2968px;font-family:var(--head);font-weight:700;font-size:16px;color:var(--navy)}
.quote-name b{color:var(--teal-dark)}
.dots{left:834px;top:3043px;display:flex;gap:7px}
.dots i{display:block;width:13px;height:13px;border-radius:50%;background:#8e98a8}
.dots i.on{background:var(--teal)}

/* footer */
.footer{left:0;top:3062px;width:1200px;height:485px;background:linear-gradient(180deg,#13306a,#0d2556)}
.foot-brand{left:172px;top:3124px;display:flex;flex-direction:column;align-items:center;gap:8px}
.foot-brand .brand-dot{background:#fff;width:60px;height:60px}
.foot-brand .brand-name{color:#fff;font-size:21px}
.social{top:3200px;width:24px;height:24px;border-radius:50%;background:var(--teal)}
.rule-h{left:169px;width:858px;height:1px;background:rgba(255,255,255,.14)}
.col h6{font-family:var(--head);font-weight:500;font-size:15px;color:var(--teal);margin-bottom:18px}
.col li{list-style:none;font-size:11px;line-height:22px;color:#fff}
.c-item{display:flex;gap:16px;font-size:11px;line-height:18px;color:#fff;margin-bottom:20px}
.copyright{left:0;top:3506px;width:1200px;text-align:center;font-size:11px;color:#fff}
</style>
</head>
<body>
<div class="page">

  <!-- hero -->
  <div class="abs hero-photo" role="img" aria-label="Woman meditating in a yoga pose on a wooden jetty over a calm sea at sunrise"></div>
  <div class="abs hero-figure" aria-hidden="true"></div>

  <div class="abs brand">
    <div class="brand-dot"></div>
    <div class="brand-name">HEARTMEADOW</div>
  </div>

  <div class="abs contact-bar" style="left:615px">
    <span class="contact-ico">
      <svg width="18" height="18" viewBox="0 0 24 24"><path d="M6.6 10.8a15 15 0 0 0 6.6 6.6l2.2-2.2c.3-.3.7-.4 1-.2 1.1.4 2.3.6 3.6.6.6 0 1 .4 1 1V20c0 .6-.4 1-1 1A17 17 0 0 1 3 4c0-.6.4-1 1-1h3.5c.6 0 1 .4 1 1 0 1.3.2 2.5.6 3.6.1.3 0 .7-.2 1z" fill="var(--teal)"/></svg>
    </span>
    Ph: 046 210 4400
  </div>
  <div class="abs contact-bar" style="left:803px">
    <span class="contact-ico">
      <svg width="17" height="17" viewBox="0 0 24 24"><rect x="3" y="5" width="18" height="14" rx="2" fill="none" stroke="var(--teal)" stroke-width="2"/><path d="M3 7l9 6 9-6" fill="none" stroke="var(--teal)" stroke-width="2"/></svg>
    </span>
    Email: hello@heartmeadow.se
  </div>

  <nav class="abs nav">
    <span style="left:509px">HOME</span>
    <span style="left:596px">ABOUT US</span>
    <span style="left:710px">SERVICES</span>
    <span style="left:816px">RETREATS</span>
    <span style="left:930px">CONTACT US</span>
  </nav>

  <h1 class="abs hero-title">Welcome to<br>Heartmeadow</h1>
  <div class="abs btn">READ MORE</div>
  <div class="abs slider"><i></i><i class="on"></i><i></i><i></i></div>

  <svg class="abs" style="left:0;top:600px" width="1200" height="130" viewBox="0 0 1200 130" preserveAspectRatio="none" aria-hidden="true">
    <path d="M0 105 C250 20 520 10 760 60 C930 95 1080 95 1200 70 L1200 130 L0 130Z" fill="var(--lavender-soft)"/>
    <path d="M0 105 C250 20 520 10 760 60 C900 88 1020 92 1200 78 L1200 130 L0 130Z" fill="var(--mint)" opacity=".9"/>
    <path d="M0 118 C260 40 520 30 760 70 C930 100 1080 102 1200 90 L1200 130 L0 130Z" fill="#fff"/>
  </svg>

  <!-- about -->
  <h2 class="abs sec-title" style="top:776px">ABOUT COMPANY</h2>
  <div class="abs sec-rule" style="top:818px"></div>

  <div class="abs pillar" style="left:169px;top:870px">
    <svg width="80" height="80" viewBox="0 0 80 80"><circle cx="40" cy="20" r="15" fill="none" stroke="var(--teal)" stroke-width="3"/><path d="M12 76c0-18 12-30 28-30s28 12 28 30z" fill="none" stroke="var(--teal)" stroke-width="3"/></svg>
    <h3 style="color:var(--teal-dark)">Our Body</h3>
    <p>Sed ut perspiciatis unde omnis iste naturosit voluptatem accusantium doloremque laudanium, totam rem aperiam, eaque ipsa quae ab illo intre veritatis et quasi architecto beatae vitae.</p>
    <div class="more" style="color:var(--teal-dark)">RED MORE</div>
  </div>
  <div class="abs divider-v" style="left:447px"></div>
  <div class="abs pillar" style="left:472px;top:870px">
    <svg width="80" height="80" viewBox="0 0 80 80"><circle cx="40" cy="30" r="13" fill="none" stroke="var(--lavender)" stroke-width="3"/><circle cx="40" cy="30" r="5" fill="none" stroke="var(--lavender)" stroke-width="3"/><path d="M10 34v22l16 20M70 34v22l-16 20" fill="none" stroke="var(--lavender)" stroke-width="3" stroke-linecap="round"/></svg>
    <h3 style="color:var(--lavender)">Soul</h3>
    <p>Sed ut perspiciatis unde omnis iste naturosit voluptatem accusantium doloremque laudanium, totam rem aperiam, eaque ipsa quae ab illo intre veritatis et quasi architecto beatae vitae.</p>
    <div class="more" style="color:var(--lavender)">RED MORE</div>
  </div>
  <div class="abs divider-v" style="left:755px"></div>
  <div class="abs pillar" style="left:782px;top:870px">
    <svg width="80" height="80" viewBox="0 0 80 80"><circle cx="40" cy="40" r="37" fill="none" stroke="var(--blue)" stroke-width="3"/><circle cx="40" cy="40" r="27" fill="none" stroke="var(--blue)" stroke-width="3"/><circle cx="40" cy="40" r="10" fill="none" stroke="var(--blue)" stroke-width="3"/><circle cx="22" cy="26" r="4" fill="none" stroke="var(--blue)" stroke-width="2.5"/><circle cx="65" cy="66" r="5" fill="#fff" stroke="var(--blue)" stroke-width="2.5"/></svg>
    <h3 style="color:var(--blue)">Planet</h3>
    <p>Sed ut perspiciatis unde omnis iste naturosit voluptatem accusantium doloremque laudanium, totam rem aperiam, eaque ipsa quae ab illo intre veritatis et quasi architecto beatae vitae.</p>
    <div class="more" style="color:var(--blue)">RED MORE</div>
  </div>

  <!-- services -->
  <div class="abs services-photo" role="img" aria-label="Group of people meditating together in a bright studio, under a lavender to teal colour wash"></div>
  <svg class="abs" style="left:0;top:1200px" width="1200" height="120" viewBox="0 0 1200 120" preserveAspectRatio="none" aria-hidden="true">
    <path d="M0 0 H1200 V12 C1080 70 900 110 700 100 C450 85 250 40 0 60Z" fill="#fff"/>
    <path d="M0 18 C250 0 460 40 700 88 C900 115 1080 80 1200 12 L1200 36 C1080 96 900 128 700 110 C460 80 250 40 0 40Z" fill="var(--lavender-soft)"/>
    <path d="M700 100 C900 118 1080 80 1200 12 L1200 40 C1080 100 900 126 700 108Z" fill="var(--mint)"/>
  </svg>
  <h2 class="abs sec-title" style="top:1333px;color:#fff">SERVICES</h2>
  <div class="abs sec-rule" style="top:1380px;background:#fff"></div>

  <div class="abs svc" style="left:159px;top:1438px">
    <svg width="66" height="66" viewBox="0 0 66 66" fill="#fff"><rect x="30" y="4" width="32" height="22" rx="2"/><circle cx="16" cy="12" r="6"/><rect x="10" y="20" width="12" height="22" rx="3"/><circle cx="16" cy="50" r="5"/><circle cx="33" cy="50" r="5"/><circle cx="50" cy="50" r="5"/><rect x="8" y="57" width="50" height="6" rx="3"/></svg>
    <h4>Coaching</h4>
    <p>Sed ut perspiciatis unde omnis is nat urosit voluptatem accusantiumoor emque laudanium, totam rem aperim, eaque ipsa quae ab lprillo intre.</p>
  </div>
  <div class="abs svc" style="left:382px;top:1438px">
    <svg width="66" height="66" viewBox="0 0 66 66" fill="#fff"><circle cx="33" cy="10" r="8"/><path d="M24 22h18l6 22 14 10v8H4v-8l14-10z"/></svg>
    <h4>Yoga</h4>
    <p>Sed ut perspiciatis unde omnis is nat urosit voluptatem accusantiumoor emque laudanium, totam rem aperim, eaque ipsa quae ab lprillo intre.</p>
  </div>
  <div class="abs svc" style="left:606px;top:1438px">
    <svg width="66" height="66" viewBox="0 0 66 66" fill="#fff"><circle cx="30" cy="10" r="7"/><rect x="6" y="32" width="56" height="10" rx="5"/><circle cx="14" cy="27" r="6"/><rect x="24" y="20" width="30" height="10" rx="5"/><rect x="10" y="44" width="5" height="18"/><rect x="52" y="44" width="5" height="18"/></svg>
    <h4>Massage</h4>
    <p>Sed ut perspiciatis unde omnis is nat urosit voluptatem accusantiumoor emque laudanium, totam rem aperim, eaque ipsa quae ab lprillo intre.</p>
  </div>
  <div class="abs svc" style="left:831px;top:1438px">
    <svg width="66" height="66" viewBox="0 0 66 66" fill="#fff"><path d="M33 18c-8-6-24-4-24 16 0 16 12 30 24 28 12 2 24-12 24-28 0-20-16-22-24-16z"/><path d="M33 18c0-8 4-13 10-15" stroke="#fff" stroke-width="3" fill="none"/></svg>
    <h4>Healthy Food</h4>
    <p>Sed ut perspiciatis unde omnis is nat urosit voluptatem accusantiumoor emque laudanium, totam rem aperim, eaque ipsa quae ab lprillo intre.</p>
  </div>

  <div class="abs svc" style="left:286px;top:1664px">
    <svg width="66" height="66" viewBox="0 0 66 66" fill="#fff"><rect x="4" y="8" width="6" height="18" rx="2"/><rect x="56" y="8" width="6" height="18" rx="2"/><rect x="8" y="14" width="50" height="5"/><circle cx="33" cy="26" r="7"/><path d="M22 34h22l-4 14 8 14h-8l-7-12-7 12h-8l8-14z"/></svg>
    <h4>Retreats</h4>
    <p>Sed ut perspiciatis unde omnis is nat urosit voluptatem accusantiumoor emque laudanium, totam rem aperim, eaque ipsa quae ab lprillo intre.</p>
  </div>
  <div class="abs svc" style="left:507px;top:1664px">
    <svg width="66" height="66" viewBox="0 0 66 66" fill="#fff"><path d="M6 32h54c0 16-12 28-27 28S6 48 6 32z"/><rect x="34" y="6" width="8" height="28" rx="4" transform="rotate(30 38 20)"/><circle cx="14" cy="18" r="2.5"/><circle cx="22" cy="10" r="2"/><circle cx="8" cy="8" r="2"/></svg>
    <h4>Healing</h4>
    <p>Sed ut perspiciatis unde omnis is nat urosit voluptatem accusantiumoor emque laudanium, totam rem aperim, eaque ipsa quae ab lprillo intre.</p>
  </div>
  <div class="abs svc" style="left:732px;top:1664px">
    <svg width="80" height="66" viewBox="0 0 80 66"><ellipse cx="34" cy="26" rx="28" ry="21" fill="none" stroke="#fff" stroke-width="5"/><path d="M18 42l-6 14 16-9" fill="#fff"/><path d="M58 20c10 4 16 12 14 22l4 14-14-6" fill="none" stroke="#fff" stroke-width="5"/></svg>
    <h4>Inspirational<br>Talks</h4>
    <p>Sed ut perspiciatis unde omnis is nat urosit voluptatem accusantiumoor emque laudanium, totam rem ape</p>
  </div>

  <svg class="abs" style="left:0;top:1950px" width="1200" height="60" viewBox="0 0 1200 60" preserveAspectRatio="none" aria-hidden="true">
    <path d="M0 42 C300 26 700 20 1200 22 V60 H0Z" fill="var(--lavender-soft)"/>
    <path d="M0 30 C300 20 600 18 1200 28 V60 H0Z" fill="var(--mint)"/>
    <path d="M0 52 C320 38 700 30 1200 40 V60 H0Z" fill="#fff"/>
  </svg>

  <!-- blog -->
  <h2 class="abs sec-title" style="top:2048px;color:#333a44">LATEST BLOG</h2>
  <div class="abs sec-rule" style="top:2097px"></div>

  <div class="abs blog-img" style="left:172px;top:2149px;width:414px;height:276px;background:linear-gradient(135deg,#cfd8c8,#e9dfd6 50%,#b9cfa4)" role="img" aria-label="Smiling woman eating a fresh salad in a bright kitchen"></div>
  <div class="abs post" style="left:172px;top:2446px;width:414px">
    <h5>SED UT PERSPICIATIS UNOMNIS</h5>
    <p style="margin-top:8px">Sed ut perspiciatis undloree omnis iste natus error sit voluptatem accusaloren tium doloremque laudantium, totloram rem aperiam, eaque ipsa.</p>
    <div class="date" style="margin-top:8px">APR 28 2019</div>
  </div>

  <div class="abs blog-img" style="left:605px;top:2149px;width:205px;height:186px;background:linear-gradient(135deg,#e8ddd3,#c99b7f 55%,#f1ece8)" role="img" aria-label="Woman relaxing during a back massage"></div>
  <div class="abs post" style="left:827px;top:2162px;width:200px">
    <h5>SED UT PER SPICIATIS<br>UNDE OMNIS ISTE</h5>
    <p style="margin-top:10px">Sed ut perspiciatis undloree omnis iste natus error sit voluptatem accusaloren tium doloremque laudantium, totloram rem aperiam, eaque ipsa.</p>
    <div class="date" style="margin-top:10px;margin-left:3px">APR 25 2019</div>
  </div>

  <div class="abs blog-img" style="left:605px;top:2354px;width:205px;height:186px;background:linear-gradient(135deg,#d7e4ee,#b8c9d6 50%,#8fb0c6)" role="img" aria-label="Group yoga class with arms raised above their heads"></div>
  <div class="abs post" style="left:827px;top:2367px;width:200px">
    <h5>SED UT PER SPICIATIS<br>UNDE OMNIS ISTE</h5>
    <p style="margin-top:10px">Sed ut perspiciatis undloree omnis iste natus error sit voluptatem accusaloren tium doloremque laudantium, totloram rem aperiam, eaque ipsa.</p>
    <div class="date" style="margin-top:10px;margin-left:3px">APR 25 2019</div>
  </div>

  <!-- testimonial -->
  <div class="abs quote-band"></div>
  <svg class="abs" style="left:0;top:2640px" width="1200" height="120" viewBox="0 0 1200 120" preserveAspectRatio="none" aria-hidden="true">
    <path d="M0 0 H1200 V10 C1000 70 700 110 400 80 C250 65 120 60 0 62Z" fill="#fff"/>
    <path d="M0 36 C200 30 420 40 620 60 C850 80 1050 60 1200 14 L1200 30 C1050 80 850 100 620 84 C420 66 200 56 0 62Z" fill="var(--lavender-soft)"/>
    <path d="M620 66 C850 88 1050 62 1200 14 L1200 34 C1050 84 850 104 620 80Z" fill="var(--mint)"/>
  </svg>
  <div class="abs ghost-quote" style="left:40px;top:2740px">“</div>
  <div class="abs quote-mark" style="left:230px;top:2800px">“</div>
  <p class="abs quote-text">Sed ut perspiciatis unde omnis iste natus error sit voluptatem accusantium doloremque laudantium, totam rem aperiam, eaque ipsa quae ab illo inventore veritatis et quasi archito beatae vitae dicta sunt explicabo. Nemo enim ipsam voluptatem quia voluptas sit aspernaur aut odit aut fugit, sed quia consequuntur magni dolores eos qui ratione voluptatem sequi nesciunt. Neque porro quisquam est, qui dolorem ipsum quia dolor sit ame.</p>
  <div class="abs quote-mark" style="left:830px;top:2935px">”</div>
  <div class="abs quote-name"><b>-Elin</b> Berg</div>
  <div class="abs dots"><i></i><i></i><i class="on"></i><i></i></div>

  <!-- footer -->
  <div class="abs footer"></div>
  <svg class="abs" style="left:0;top:3050px" width="1200" height="70" viewBox="0 0 1200 70" preserveAspectRatio="none" aria-hidden="true">
    <path d="M0 0 H1200 V6 C1000 40 760 56 520 40 C330 28 160 18 0 24Z" fill="var(--mist)"/>
    <path d="M0 24 C200 16 400 34 560 46 C800 62 1020 44 1200 6 L1200 22 C1020 60 800 76 560 60 C400 48 200 32 0 40Z" fill="var(--lavender-soft)"/>
    <path d="M560 50 C800 66 1020 46 1200 6 L1200 26 C1020 64 800 80 560 62Z" fill="var(--mint)"/>
  </svg>
  <div class="abs foot-brand">
    <div class="brand-dot"></div>
    <div class="brand-name">HEARTMEADOW</div>
  </div>
  <div class="abs social" style="left:940px"></div>
  <div class="abs social" style="left:970px"></div>
  <div class="abs social" style="left:1001px"></div>
  <div class="abs rule-h" style="top:3254px"></div>

  <div class="abs col" style="left:169px;top:3278px;width:240px">
    <h6>Contact</h6>
    <div class="c-item">
      <svg width="20" height="24" viewBox="0 0 20 24"><path d="M10 1a8 8 0 0 0-8 8c0 6 8 14 8 14s8-8 8-14a8 8 0 0 0-8-8z" fill="none" stroke="var(--teal)" stroke-width="1.5"/><circle cx="10" cy="9" r="3" fill="none" stroke="var(--teal)" stroke-width="1.5"/></svg>
      <span>12 Ängsvägen,<br>Lund, Skåne</span>
    </div>
    <div class="c-item" style="margin-top:8px">
      <svg width="24" height="24" viewBox="0 0 24 24"><path d="M6.6 10.8a15 15 0 0 0 6.6 6.6l2.2-2.2c.3-.3.7-.4 1-.2 1.1.4 2.3.6 3.6.6.6 0 1 .4 1 1V20c0 .6-.4 1-1 1A17 17 0 0 1 3 4c0-.6.4-1 1-1h3.5c.6 0 1 .4 1 1 0 1.3.2 2.5.6 3.6.1.3 0 .7-.2 1z" fill="none" stroke="var(--teal)" stroke-width="1.3"/></svg>
      <span>046 210 4401<br>046 210 4402</span>
    </div>
    <div class="c-item" style="margin-top:8px">
      <svg width="26" height="20" viewBox="0 0 26 20"><rect x="1" y="2" width="24" height="16" rx="1" fill="none" stroke="var(--teal)" stroke-width="1.5"/><path d="M1 3l12 9 12-9" fill="none" stroke="var(--teal)" stroke-width="1.5"/></svg>
      <span>info@heartmeadow.se<br>maria@heartmeadow.se</span>
    </div>
  </div>
  <div class="abs col" style="left:437px;top:3278px">
    <h6>Links</h6>
    <ul><li>Lorem ipsum dolo</li><li>Consectetur adipiscing elit.</li><li>Fusce eget leo tincid</li><li>Donec consequat</li><li>Praesent elementum</li><li>Jmauris posueret</li></ul>
  </div>
  <div class="abs col" style="left:654px;top:3278px">
    <h6>Information</h6>
    <ul><li>Lorem ipsum dolo</li><li>Consectetur adipiscing elit.</li><li>Fusce eget leo tincid</li><li>Donec consequat</li><li>Praesent elementum</li><li>Aenean a ex eu lectu</li></ul>
  </div>
  <div class="abs col" style="left:883px;top:3278px">
    <h6>Other Links</h6>
    <ul><li>Lorem ipsum dolo</li><li>Consectetur adipiscing elit.</li><li>Fusce eget leo tincid</li><li>Donec consequat</li><li>Praesent elementum</li><li>Aenean a ex eu lectu</li></ul>
  </div>
  <div class="abs rule-h" style="top:3482px"></div>
  <div class="abs copyright">Copyright 2019 All Rights Reserved</div>

</div>
</body>
</html>
```